Building company buisness cards

We are looking for a sharp modern new look for our business cards.We are a New Zealand based company that specialises in house and land packages.We have attached a photo of the current logo and would like to see if it can be improved somehow if needed.We are open to any colours but we have chosen Black and White at this stage. Feel free to change the font and make the logo smarter looking.Play with the colours and see what looks best.We want a card that looks so good know one will want to throw it away!

Target Market(s)

Building profesonals, home buyers

Industry/Entity Type

Building

Contact Information for Business Card

Garrick Tenwood
0275390628
garrickt@hartvale.co.nz

Font styles to use
Serif
Sans Serif

Colors

Designer to choose colors to be used in the design.

Requirements
Must have
• Just the logo on one side and details on the other
• Clean simple looking card
Nice to have
• Round corners and detail like raised or spot UV
• Something that stands out
Should not have
• To title needed, Director etc

```html
<!DOCTYPE html>
<html lang="en">
<head>
<meta charset="utf-8">
<title>Hartvale business cards</title>
<link href="https://fonts.googleapis.com/css2?family=Open+Sans:wght@400;600;700&display=swap" rel="stylesheet">
<style>
  :root{
    --stage:#2b2b2d;
    --card-dark:#1c1c1d;
    --card-light:#ffffff;
    --ink:#111111;
    --ink-soft:#333333;
    --paper:#f4f4f4;
    --notch:#151515;
  }
  *{box-sizing:border-box;margin:0;padding:0}
  html,body{width:1200px;height:885px;overflow:hidden}
  body{background:var(--stage);font-family:"Open Sans",Arial,sans-serif;position:relative}
  .card{position:absolute;left:290px;width:620px;height:354px;border-radius:22px;overflow:hidden}
  .card--back{top:48px;background:var(--card-dark);color:var(--paper)}
  .card--front{top:484px;background:var(--card-light);color:var(--ink)}

  .back-mark{position:absolute;left:0;right:0;top:118px;display:flex;justify-content:center;align-items:center;gap:12px}
  .back-mark .ring{width:34px;height:34px;border:3px solid var(--paper);border-radius:50%}
  .back-mark .brand{font-weight:600;font-size:26px;letter-spacing:1px}
  .back-web{position:absolute;left:0;right:0;top:280px;text-align:center;font-size:15px;letter-spacing:7px}

  .notch{position:absolute;top:74px;width:18px;height:38px;background:var(--notch);border-radius:9px}
  .notch--left{left:-9px}
  .notch--right{right:-9px}

  .holder{position:absolute;left:48px;top:78px}
  .holder .name{font-weight:700;font-size:20px;line-height:1.2}
  .holder .web{font-weight:600;font-size:16px;color:var(--ink-soft)}

  .front-mark{position:absolute;left:0;right:0;top:148px;display:flex;justify-content:center;align-items:center;gap:12px}
  .front-mark .brand{font-weight:700;font-size:50px;letter-spacing:-1px}
  .front-mark .ring{width:46px;height:46px;border:3px solid var(--ink);border-radius:50%}

  .contact{position:absolute;right:36px;top:56px;text-align:right;font-size:15px;color:var(--ink-soft);line-height:1.5}
  .contact li{list-style:none;display:flex;justify-content:flex-end;align-items:center;gap:6px}
  .contact svg{width:14px;height:14px;fill:var(--ink)}
</style>
</head>
<body>
  <section class="card card--back" aria-label="Card back">
    <div class="back-mark"><span class="ring"></span><span class="brand">Hartvale</span></div>
    <p class="back-web">www.hartvale.co.nz</p>
  </section>

  <section class="card card--front" aria-label="Card front">
    <span class="notch notch--left"></span>
    <span class="notch notch--right"></span>
    <div class="holder">
      <p class="name">Garrick Tenwood</p>
      <p class="web">www.hartvale.co.nz</p>
    </div>
    <div class="front-mark"><span class="brand">Hartvale</span><span class="ring"></span></div>
    <ul class="contact">
      <li>0275390628
        <svg viewBox="0 0 16 16" aria-hidden="true"><path d="M2 5c0-2 2-3 6-3s6 1 6 3v1h-3V5H5v1H2zM4 7h8l2 6H2z"/></svg>
      </li>
      <li>garrickt@hartvale.co.nz
        <svg viewBox="0 0 16 16" aria-hidden="true"><path d="M1 4h14v9H1zM1 4l7 5 7-5" stroke="#fff" stroke-width="1"/></svg>
      </li>
    </ul>
  </section>
</body>
</html>
```